Harrowmere Freight, Project

Company Profile
Harrowmere Freight Sdn Bhd is a well established and experienced freight forwarder in Kuala Lumpur, Malaysia. We specialize in air and sea forwarding, Custom Brokerage and regulatory compliance services, inland transportation,
overseas freighting and warehousing and distribution management. With our dedicated qualified and experienced professionals, we are fully committed to serving our clients.

Our Mission
Based on the motto “Quick, Reliable and Polite”, Harrowmere Freight is dedicated to upholding the following three points corporate philosophy:
1. Adhering to the principle that “the customer always comes first”.
2. Contributing to the development of the local community.
3. Making it our duty to be responsible and sincere.

Our Edge
• One-Stop Logistics Solutions
• Extensive Network Throughout Malaysia
• Highly Qualified and Experienced Pool of Professionals
• Comprehensive IT Solutions
• Innovative and Customer-focused Solutions
• Flexible and Consistent in Managing Exceptions
• Total Supply Chain Visibility

Target Market(s)

We sell the logistics services to all the industry in Malaysia. (ONE Stop Logistics Solutions)

Industry/Entity Type

Logistic

Contact Information for Business Card

I want the back of the card to be white with the logo and slogan. i would like to see the logo on the front with the general info.

Requirements
Must have
• Name, Title, Office, Cell, Fax, Email, Address, Website
Nice to have
• Modern Design Business Card

```html
<!DOCTYPE html>
<html lang="en">
<head>
<meta charset="utf-8">
<title>Harrowmere Freight — Stationery</title>
<link href="https://fonts.googleapis.com/css2?family=Open+Sans:wght@400;600;700&display=swap" rel="stylesheet">
<style>
  :root{
    --bg:#262626;
    --blue:#1f8fdc;
    --blue-deep:#1466c4;
    --blue-light:#2aa6e8;
    --ink:#3a3a3a;
    --muted:#6b6b6b;
    --paper:#ffffff;
  }
  *{box-sizing:border-box;margin:0;padding:0}
  html,body{width:1200px;height:780px;overflow:hidden}
  body{background:var(--bg);font-family:"Open Sans",Arial,sans-serif;color:var(--ink);position:relative}

  .brand{font-weight:700;color:var(--blue);display:flex;align-items:center;gap:6px;white-space:nowrap}
  .brand-dot{width:9px;height:9px;border-radius:50%;background:var(--blue);flex:none}
  .brand-on-blue{color:#fff}
  .brand-on-blue .brand-dot{background:#fff}

  /* folder */
  .folder{position:absolute;left:60px;top:210px;width:400px;height:520px;
    background:linear-gradient(160deg,var(--blue-light),var(--blue-deep));}
  .folder-mark{position:absolute;left:70px;top:270px;width:150px;height:150px;border-radius:50%;background:rgba(255,255,255,.18)}

  /* letterhead */
  .letterhead{position:absolute;left:190px;top:60px;width:420px;height:594px;background:var(--paper);
    padding:38px 48px 28px;display:flex;flex-direction:column;box-shadow:0 6px 18px rgba(0,0,0,.35)}
  .letterhead .brand{justify-content:center;font-size:15px}
  .letter-body{margin-top:46px;font-size:7.6px;line-height:1.75;color:var(--ink)}
  .letter-body p{margin-bottom:12px}
  .sign{margin-top:14px;align-self:flex-end;text-align:right;width:130px}
  .sign-mark{height:26px;background:linear-gradient(90deg,#eef2f6,#dfe5ec);border-radius:3px}
  .sign-name{font-size:7.5px;letter-spacing:.5px;margin-top:4px}
  .letter-foot{margin-top:auto;text-align:center;font-size:6.6px;line-height:1.6}
  .letter-foot .co{color:var(--blue);font-weight:700}
  .letter-foot .lab{color:var(--blue)}

  /* cards */
  .card{position:absolute;width:250px;height:143px;box-shadow:0 5px 14px rgba(0,0,0,.35)}
  .card-blue{background:linear-gradient(170deg,var(--blue-light),var(--blue-deep));color:#fff;padding:14px 16px;display:flex;flex-direction:column}
  .card-blue h4{font-size:8px;text-align:center;font-weight:700;margin-bottom:4px}
  .card-blue .services{font-size:5.6px;line-height:1.55}
  .card-blue .card-mark{margin:10px auto 0;width:26px;height:26px;border-radius:50%;background:rgba(255,255,255,.3)}
  .card-blue .slogan{margin-top:auto;text-align:center;font-size:7px;font-weight:700;letter-spacing:.3px}
  .card-white{background:var(--paper);padding:14px 16px;display:flex;flex-direction:column;align-items:center}
  .card-white .brand{font-size:9px}
  .card-white .name{margin-top:8px;font-size:10px;font-weight:700;color:var(--blue)}
  .card-white .title{font-size:6.5px;color:var(--ink)}
  .card-white .cell{font-size:5.5px;color:var(--muted)}
  .card-white .contact{margin-top:8px;font-size:5.2px;line-height:1.55;text-align:left;width:100%}
  .card-white .contact b{color:var(--blue);font-weight:700}
  .card-white .contact .lab{color:var(--blue)}
  .card-white .slogan{margin-top:auto;font-size:6.5px;font-weight:600;color:var(--ink);letter-spacing:.4px}

  /* envelope */
  .envelope{position:absolute;left:650px;top:410px;width:520px;height:260px;background:var(--paper);
    box-shadow:0 6px 18px rgba(0,0,0,.35);display:flex;align-items:center;justify-content:center}
  .envelope .brand{font-size:22px;margin-top:-30px}
  .envelope .band{position:absolute;left:0;right:0;bottom:0;height:22px;background:var(--blue-light)}
</style>
</head>
<body>

<div class="folder">
  <div class="folder-mark"></div>
</div>

<article class="letterhead">
  <div class="brand"><span class="brand-dot"></span>Harrowmere Freight</div>
  <div class="letter-body">
    <p>Lorem Ipsum is simply dummy text of the printing and typesetting industry. Lorem Ipsum has been the industry's standard dummy text ever since the 1500s, when an unknown printer took a galley of type and scrambled it to make a type specimen book. It has survived not only five centuries, but also the leap into electronic typesetting, remaining essentially unchanged. It was popularised in the 1960s with the release of Letraset sheets containing Lorem Ipsum passages, and more recently with desktop publishing software like Aldus PageMaker including versions of Lorem Ipsum.</p>
    <p>Established fact that a reader will be distracted by the readable content of a page when looking at its layout. The point of using Lorem Ipsum is that it has a more-or-less normal distribution of letters, as opposed to using 'Content here, content here', making it look like readable English.</p>
    <p>Many desktop publishing packages and web page editors now use Lorem Ipsum as their default model text, and a search for 'lorem ipsum' will uncover many web sites still in their infancy. Various versions have evolved over the years, sometimes by accident, sometimes on purpose (injected humour and the like).</p>
  </div>
  <div class="sign">
    <div class="sign-mark" role="img" aria-label="Handwritten signature"></div>
    <div class="sign-name">IDRIS HALIM</div>
  </div>
  <footer class="letter-foot">
    <div class="co">HARROWMERE FREIGHT SDN BHD</div>
    <div><span class="lab">Address:</span> No. 14B, 2nd Floor, Jalan Seroja 3, Taman Seroja Indah, 41050 Klang, Selangor, Malaysia.</div>
    <div><span class="lab">Tel:</span> (60) 3 3350 2140 • <span class="lab">Fax:</span> (60) 3 3350 2141 • <span class="lab">Email:</span> enquiry@harrowmere.com.my</div>
    <div><span class="lab">GST Registration No:</span> 000518204776</div>
  </footer>
</article>

<section class="card card-blue" style="left:650px;top:60px">
  <h4>We're Specialize In</h4>
  <div class="services">• International Shipping (Air/Sea) • Supply Chain Management • Tax Exemption Consultancy (Customs) • Transportation (Haulage) • Packing • Consolidation • NVOCC • Project Management • Marine Insurance • Warehousing • Distribution • Custom Brokerage • Door to Door</div>
  <div class="card-mark"></div>
  <div class="slogan">ONE STOP LOGISTICS SOLUTIONS</div>
</section>

<section class="card card-white" style="left:920px;top:60px">
  <div class="brand"><span class="brand-dot"></span>Harrowmere Freight</div>
  <div class="name">Faizal Rahmat</div>
  <div class="title">Managing Director</div>
  <div class="cell">Cell: (60) 12 418 7730</div>
  <div class="contact">
    <b>HARROWMERE FREIGHT SDN BHD</b><br>
    <span class="lab">Office:</span> No. 14B, 2nd Floor, Jalan Seroja 3, Taman Seroja Indah, 41050 Klang, Selangor<br>
    <span class="lab">Tel:</span> (60) 3 3350 2140 • <span class="lab">Fax:</span> (60) 3 3350 2141 • faizal@harrowmere.com.my • www.harrowmere.com.my
  </div>
  <div class="slogan">ONE STOP LOGISTICS SOLUTIONS</div>
</section>

<section class="card card-white" style="left:650px;top:223px">
  <div class="brand"><span class="brand-dot"></span>Harrowmere Freight</div>
  <div class="name">Faizal Rahmat</div>
  <div class="title">Managing Director</div>
  <div class="cell">Cell: (60) 12 418 7730</div>
  <div class="contact">
    <b>HARROWMERE FREIGHT SDN BHD</b><br>
    <span class="lab">Office:</span> No. 14B, 2nd Floor, Jalan Seroja 3, Taman Seroja Indah, 41050 Klang, Selangor<br>
    <span class="lab">Tel:</span> (60) 3 3350 2140 • <span class="lab">Fax:</span> (60) 3 3350 2141 • faizal@harrowmere.com.my • www.harrowmere.com.my
  </div>
  <div class="slogan">ONE STOP LOGISTICS SOLUTIONS</div>
</section>

<section class="card card-blue" style="left:920px;top:223px">
  <h4>We're Specialize In</h4>
  <div class="services">• International Shipping (Air/Sea) • Supply Chain Management • Tax Exemption Consultancy (Customs) • Transportation (Haulage) • Packing • Consolidation • NVOCC • Project Management • Marine Insurance • Warehousing • Distribution • Custom Brokerage • Door to Door</div>
  <div class="card-mark"></div>
  <div class="slogan">ONE STOP LOGISTICS SOLUTIONS</div>
</section>

<section class="envelope">
  <div class="brand"><span class="brand-dot"></span>Harrowmere Freight</div>
  <div class="band"></div>
</section>

</body>
</html>
```